Business Card Design

We are a residential half way house for the addict ,the alcoholic and dual diagnosed in recovery.
i house both men and woman age 18+

Industry/Entity Type

Residential

```html
<!DOCTYPE html>
<html lang="en">
<head>
<meta charset="utf-8">
<title>Marigold's Family Sober House – Business Card</title>
<link href="https://fonts.googleapis.com/css2?family=Anton&family=Roboto+Condensed:wght@300;400&display=swap" rel="stylesheet">
<style>
  :root {
    --page-bg: #e9e6e1;
    --card-top: #ffffff;
    --card-bottom: #d9d9d9;
    --ink: #1a1a1a;
    --ink-soft: #2b2b2b;
    --accent-red: #d2161f;
    --accent-red-dark: #a8121a;
    --rule: #111111;
  }
  html, body {
    margin: 0;
    width: 1200px;
    height: 892px;
    overflow: hidden;
    background: var(--page-bg);
  }
  .business-card {
    position: absolute;
    left: 100px;
    top: 156px;
    width: 1000px;
    height: 580px;
    background: linear-gradient(170deg, var(--card-top) 0%, #f1f1f1 40%, var(--card-bottom) 100%);
    box-shadow: 0 10px 30px rgba(0,0,0,0.25);
    overflow: hidden;
  }
  .brand-name {
    position: absolute;
    left: 70px;
    top: 90px;
    margin: 0;
    font-family: 'Anton', sans-serif;
    font-weight: 400;
    color: var(--ink);
    line-height: 1;
    letter-spacing: 0.5px;
  }
  .brand-name .brand-line-1 { display: block; font-size: 72px; }
  .brand-name .brand-line-2 { display: block; font-size: 44px; margin-left: 44px; }
  .owner {
    position: absolute;
    left: 180px;
    top: 300px;
    font-family: 'Roboto Condensed', sans-serif;
    color: var(--ink-soft);
  }
  .owner-name { margin: 0; font-size: 64px; font-weight: 300; line-height: 1; }
  .owner-title { margin: 8px 0 0 26px; font-size: 21px; font-weight: 400; line-height: 1.15; }
  .contact-list {
    position: absolute;
    right: 40px;
    top: 256px;
    margin: 0;
    padding: 0;
    list-style: none;
    font-family: 'Roboto Condensed', sans-serif;
    font-size: 24px;
    color: var(--ink);
  }
  .contact-list li {
    display: flex;
    justify-content: flex-end;
    align-items: center;
    gap: 14px;
    height: 38px;
  }
  .contact-icon {
    width: 26px;
    height: 26px;
    flex: none;
  }
  .contact-rule {
    position: absolute;
    left: 0;
    right: 0;
    top: 470px;
    height: 3px;
    background: var(--rule);
  }
  .accent-band {
    position: absolute;
    left: 0;
    right: 0;
    top: 480px;
    bottom: 0;
    background: linear-gradient(180deg, var(--accent-red) 0%, var(--accent-red-dark) 100%);
  }
</style>
</head>
<body>
  <div class="business-card">
    <h1 class="brand-name">
      <span class="brand-line-1">Marigold's</span>
      <span class="brand-line-2">Family Sober House Inc</span>
    </h1>

    <div class="owner">
      <p class="owner-name">Dana Whitfield</p>
      <p class="owner-title">Owner<br>(15 yrs.in recovery)</p>
    </div>

    <ul class="contact-list">
      <li>(555) 014-0305
        <svg class="contact-icon" viewBox="0 0 26 26" aria-hidden="true"><rect width="26" height="26" rx="5" fill="var(--accent-red)"/><path d="M8 7c1-1 2-1 2.5 0l1.2 2.3c.3.6 0 1.2-.5 1.5l-.8.5c.7 1.6 2 2.9 3.6 3.6l.5-.8c.3-.5.9-.8 1.5-.5L18.3 15c1 .5 1 1.5 0 2.5-1 1-2.3 1.4-4 .6-3-1.4-5.3-3.7-6.7-6.7C6.8 9.6 7 8 8 7z" fill="var(--ink)"/></svg>
      </li>
      <li>(555) 014-0306
        <svg class="contact-icon" viewBox="0 0 26 26" aria-hidden="true"><rect width="26" height="26" rx="5" fill="var(--accent-red)"/><path d="M8 7c1-1 2-1 2.5 0l1.2 2.3c.3.6 0 1.2-.5 1.5l-.8.5c.7 1.6 2 2.9 3.6 3.6l.5-.8c.3-.5.9-.8 1.5-.5L18.3 15c1 .5 1 1.5 0 2.5-1 1-2.3 1.4-4 .6-3-1.4-5.3-3.7-6.7-6.7C6.8 9.6 7 8 8 7z" fill="var(--ink)"/></svg>
      </li>
      <li>(555) 019-5536
        <svg class="contact-icon" viewBox="0 0 26 26" aria-hidden="true"><rect width="26" height="26" rx="5" fill="var(--accent-red)"/><rect x="9" y="6" width="8" height="4" fill="var(--ink)"/><rect x="6" y="10" width="14" height="7" rx="1" fill="var(--ink)"/><rect x="9" y="15" width="8" height="5" fill="var(--ink)" stroke="var(--accent-red)" stroke-width="1"/></svg>
      </li>
      <li>danawhitfield@example.com
        <svg class="contact-icon" viewBox="0 0 26 26" aria-hidden="true"><rect width="26" height="26" rx="5" fill="var(--accent-red)"/><rect x="6" y="8" width="14" height="10" fill="var(--ink)"/><path d="M6 8l7 6 7-6" fill="none" stroke="var(--accent-red)" stroke-width="1.4"/></svg>
      </li>
      <li>2740 Seagrape Rd. Bay Haven,Fla 30000
        <svg class="contact-icon" viewBox="0 0 26 26" aria-hidden="true"><rect width="26" height="26" rx="5" fill="var(--accent-red)"/><path d="M13 21s-5-5.5-5-9a5 5 0 0 1 10 0c0 3.5-5 9-5 9z" fill="var(--ink)"/><circle cx="13" cy="12" r="1.8" fill="var(--accent-red)"/></svg>
      </li>
    </ul>

    <div class="contact-rule"></div>
    <div class="accent-band"></div>
  </div>
</body>
</html>
```